Infection control

to re-design website to include the benefits of powdered bleach packed in pre-measured sachets which when dissolved in water provides economy, efficacy and is safe to use with the use of costly packaging. We need new text outlining the benefits of the world's most commonly used disinfectant for major hospitals, institutions, pathology, military and disaster areas.

Translate design into coded website using CMS with the following features:
Mobile responsive using HTML 5/ CSS3 standards
Coded with SEO standards and with H1 tags for easy spidering and with Wordpress CMS with is page rank 9
Site migration
Email support
Updates

Target Market(s)

hospitals, institutions, pathology, military and disaster areas

Industry/Entity Type

Chemical Product

Number of Pages Required

4 page

Colors

Designer to choose colors to be used in the design.

Requirements
Must have
• factual information based on the efficiency of sodium hypochlorite (bleach) used for infection control. The many viruses, bacteria, pathogens etc which certain strengths of bleach eliminate upon contact.
• As tis is a redesign, existing pages including MSDS sheets to stay the same
Nice to have
• a new look and feel including current logos
Should not have
• incorrect info

```html
<!DOCTYPE html>
<html lang="en">
<head>
<meta charset="utf-8">
<title>Sanivex – Hospital Grade Infection Control</title>
<link rel="stylesheet" href="https://fonts.googleapis.com/css2?family=Montserrat:wght@400;500;600;700&family=Raleway:wght@400;500;600&display=swap">
<style>
:root{
  --green:#69b823;
  --green-dark:#4f9a12;
  --ink:#111111;
  --charcoal:#2a2c2e;
  --grey-card:#ececec;
  --text:#444444;
  --muted:#666666;
  --white:#ffffff;
  --head:"Montserrat", sans-serif;
  --body:"Raleway", sans-serif;
}
*{margin:0;padding:0;box-sizing:border-box}
html,body{width:1200px;height:3220px;overflow:hidden;background:var(--white)}
body{position:relative;font-family:var(--body);color:var(--text)}
.abs{position:absolute}

/* header */
.site-header{position:absolute;left:0;top:0;width:1200px;height:125px;background:var(--white)}
.brand{position:absolute;left:77px;top:30px;display:flex;align-items:center;gap:10px}
.brand-dot{width:40px;height:40px;border-radius:50%;background:var(--green)}
.brand-name{font-family:var(--head);font-weight:600;font-size:44px;color:var(--green);line-height:1}
.main-nav{position:absolute;left:340px;top:0;height:125px;font-family:var(--body);font-size:16px;color:#555}
.main-nav a{position:absolute;top:0;height:125px;display:flex;align-items:center;color:inherit;text-decoration:none;white-space:nowrap}
.main-nav .is-active{background:var(--green);color:var(--white);width:84px;justify-content:center}
.phone-btn{position:absolute;left:977px;top:39px;width:146px;height:47px;background:var(--green);color:var(--white);font-family:var(--body);font-size:16px;display:flex;align-items:center;justify-content:center;gap:10px}

/* hero */
.hero-bg{position:absolute;left:0;top:125px}
.hero-title{position:absolute;left:175px;top:318px;width:850px;text-align:center;font-family:var(--head);font-weight:700;font-size:36px;line-height:42px;color:var(--white)}
.btn{position:absolute;background:var(--green);color:var(--white);font-family:var(--head);font-size:18px;display:flex;align-items:center;justify-content:center;letter-spacing:.3px}
.hero-btn{left:515px;top:487px;width:168px;height:58px}

.seal{position:absolute;width:100px;height:100px;border-radius:50%;background:var(--white);border:6px solid var(--green);display:flex;align-items:center;justify-content:center}
.seal span{width:56px;height:56px;border-radius:50%;background:var(--green)}

/* section titles */
.section-title{position:absolute;left:0;width:1200px;text-align:center;font-family:var(--head);font-weight:600;font-size:36px;color:var(--ink)}
.section-title em{font-style:normal;color:var(--green)}
.title-rule{position:absolute;height:2px;background:#cfcfcf}

/* feature cards */
.feature{position:absolute;top:919px;width:314px}
.feature h3{height:51px;background:var(--ink);color:var(--white);font-family:var(--body);font-weight:500;font-size:22px;display:flex;align-items:center;justify-content:center;letter-spacing:.5px}
.feature p{position:absolute;top:70px;left:28px;width:258px;text-align:center;font-size:13px;line-height:25px;color:var(--white)}
.feature svg.shape{display:block}
.feature .icon{position:absolute;left:114px;top:201px;width:86px;height:86px;border-radius:50%;background:var(--white);border:5px solid var(--green);display:flex;align-items:center;justify-content:center}

/* benefits */
.benefits-bg{position:absolute;left:0;top:1255px}
.benefits-title{color:var(--green)}
.benefit-label{position:absolute;font-family:var(--body);font-size:23px;color:var(--white)}
.node{position:absolute;border-radius:50%;border:6px solid var(--green);background:linear-gradient(135deg,#a9b8c4,#6d7f8e)}

/* products */
.product{position:absolute;top:2147px;width:509px;height:311px}
.product .body{height:251px;background:var(--grey-card);border-radius:14px 14px 0 0;position:relative}
.product .pack{position:absolute;left:15px;top:56px;width:142px;height:142px;border-radius:50%;background:linear-gradient(135deg,#ffffff,#e9e3c8);box-shadow:0 2px 10px rgba(0,0,0,.18)}
.product p{position:absolute;left:172px;top:40px;width:318px;font-size:14px;line-height:25.5px;color:var(--text)}
.product h3{height:60px;background:var(--green);color:var(--white);font-family:var(--head);font-weight:700;font-size:32px;display:flex;align-items:center;justify-content:center;border-radius:0 0 10px 10px}

/* footer */
.footer-bg{position:absolute;left:0;top:2560px}
.footer-heading{position:absolute;top:2688px;font-family:var(--head);font-weight:600;font-size:23px;color:var(--white)}
.form-head{position:absolute;left:77px;top:2750px;width:314px;height:47px;background:var(--green);color:var(--white);font-size:20px;display:flex;align-items:center;justify-content:center}
.field{position:absolute;left:77px;width:314px;background:var(--white);font-size:12px;color:#555;padding:10px 8px}
.submit{left:77px;top:3042px;width:314px;height:52px;font-family:var(--body);font-size:19px}
.post{position:absolute;left:505px;width:275px;height:110px;border-bottom:1px solid #777}
.post .thumb{position:absolute;left:0;top:0;width:85px;height:84px;background:linear-gradient(135deg,#c7d6e0,#7f97a8)}
.post h4{position:absolute;left:103px;top:12px;font-family:var(--body);font-weight:500;font-size:16px;color:var(--white)}
.post .meta{position:absolute;left:103px;top:48px;font-size:13px;color:var(--white);display:flex;align-items:center;width:172px}
.post .meta svg{margin-left:28px;margin-right:14px}
.contact-line{position:absolute;left:861px;color:var(--white);font-size:13px;line-height:22px;display:flex;gap:16px}
.contact-line strong{font-family:var(--head);font-weight:700;font-size:13px;letter-spacing:.5px}

/* bottom bar */
.bottom-bar{position:absolute;left:0;top:3148px;width:1200px;height:72px;background:var(--green);color:var(--white);font-size:13px}
.copyright{position:absolute;left:77px;top:27px;display:flex;align-items:center;gap:12px}
.foot-nav{position:absolute;right:77px;top:27px}
.foot-nav a{color:var(--white);text-decoration:none}
.foot-nav i{font-style:normal;margin:0 10px}
</style>
</head>
<body>

<header class="site-header">
  <div class="brand"><span class="brand-dot"></span><span class="brand-name">Sanivex</span></div>
  <nav class="main-nav">
    <a class="is-active" href="#" style="left:0">Home</a>
    <a href="#" style="left:115px">About</a>
    <a href="#" style="left:190px">Products</a>
    <a href="#" style="left:288px">Downloads</a>
    <a href="#" style="left:402px">Media &amp; News</a>
    <a href="#" style="left:543px">Contact</a>
  </nav>
  <div class="phone-btn">
    <svg width="16" height="16" viewBox="0 0 24 24"><path fill="#fff" d="M6.6 10.8a15.1 15.1 0 0 0 6.6 6.6l2.2-2.2c.3-.3.7-.4 1-.2 1.1.4 2.3.6 3.6.6.6 0 1 .4 1 1V20c0 .6-.4 1-1 1A17 17 0 0 1 3 4c0-.6.4-1 1-1h3.5c.6 0 1 .4 1 1 0 1.3.2 2.5.6 3.6.1.3 0 .7-.2 1z"/></svg>
    1300 555 010
  </div>
</header>

<main>
<section class="hero">
  <svg class="hero-bg" width="1200" height="600" viewBox="0 0 1200 600" role="img" aria-label="Photo of laboratory scientists in protective glasses examining samples">
    <defs>
      <linearGradient id="heroGrad" x1="0" y1="0" x2="1" y2="1">
        <stop offset="0" stop-color="#4b5560"/>
        <stop offset=".5" stop-color="#6d7780"/>
        <stop offset="1" stop-color="#c5cbd0"/>
      </linearGradient>
    </defs>
    <polygon points="0,0 1200,0 1200,515 600,583 0,515" fill="url(#heroGrad)"/>
    <polyline points="0,515 600,583 1200,515" fill="none" stroke="var(--green)" stroke-width="6"/>
  </svg>
  <h1 class="hero-title">Our values are based on supplying quality products, on-time distribution and economy to the user.</h1>
  <a class="btn hero-btn">CONTACT US</a>
  <div class="seal" style="left:550px;top:680px"><span></span></div>
</section>

<section class="about">
  <div class="title-rule" style="left:240px;top:852px;width:130px"></div>
  <div class="title-rule" style="left:830px;top:852px;width:130px"></div>
  <h2 class="section-title" style="top:828px">About <em>Sanivex Aquaclor</em></h2>

  <div class="feature" style="left:77px">
    <h3>SAFE</h3>
    <svg class="shape" width="314" height="200" viewBox="0 0 314 200"><polygon points="0,0 314,0 314,150 157,200 0,150" fill="var(--green)"/></svg>
    <p>Aquaclor ® is both economical and convenient to use. It comes in a pre-measured powdered form which makes it easy and accurate to prepare.</p>
    <div class="icon"><svg width="44" height="44" viewBox="0 0 24 24"><path fill="#222" d="M13 2l7 3v5c0 4-3 7-7 8-4-1-7-4-7-8V5z"/><path fill="#fff" d="M10 10l2 2 4-4 1 1-5 5-3-3z"/><path fill="#222" d="M2 17h4l4 2h5v2H9l-4-2H2z"/></svg></div>
  </div>
  <div class="feature" style="left:444px">
    <h3>ECONOMICAL</h3>
    <svg class="shape" width="314" height="200" viewBox="0 0 314 200"><polygon points="0,0 314,0 314,150 157,200 0,150" fill="var(--green)"/></svg>
    <p>Aquaclor ® is both economical and convenient to use. It comes in a pre-measured powdered form which makes it easy and accurate to prepare.</p>
    <div class="icon"><svg width="48" height="48" viewBox="0 0 24 24"><circle cx="12" cy="12" r="9" fill="#222"/><g stroke="#222" stroke-width="3"><path d="M12 1v4M12 19v4M1 12h4M19 12h4M4 4l3 3M17 17l3 3M20 4l-3 3M7 17l-3 3"/></g><text x="12" y="16.5" text-anchor="middle" font-family="Montserrat, sans-serif" font-weight="700" font-size="12" fill="#fff">$</text></svg></div>
  </div>
  <div class="feature" style="left:809px">
    <h3>EFFICENT &amp; EFFECTIVE</h3>
    <svg class="shape" width="314" height="200" viewBox="0 0 314 200"><polygon points="0,0 314,0 314,150 157,200 0,150" fill="var(--green)"/></svg>
    <p>Aquaclor ® is both economical and convenient to use. It comes in a pre-measured powdered form which makes it easy and accurate to prepare.</p>
    <div class="icon"><svg width="48" height="48" viewBox="0 0 24 24"><circle cx="12" cy="12" r="11" fill="#222"/><path d="M6.5 12.5l3.5 3.5 7.5-7.5" fill="none" stroke="#fff" stroke-width="2.5"/></svg></div>
  </div>
</section>

<section class="benefits">
  <svg class="benefits-bg" width="1200" height="770" viewBox="0 0 1200 770" role="img" aria-label="Photo of a hospital corridor with medical staff and a patient trolley">
    <defs>
      <linearGradient id="benGrad" x1="0" y1="0" x2="1" y2="0">
        <stop offset="0" stop-color="#2a2f33"/>
        <stop offset=".5" stop-color="#4a5257"/>
        <stop offset="1" stop-color="#33393d"/>
      </linearGradient>
    </defs>
    <polygon points="0,119 600,16 1200,119 1200,649 600,752 0,649" fill="url(#benGrad)"/>
    <polyline points="0,127 600,24 1200,127" fill="none" stroke="var(--green)" stroke-width="12"/>
    <polyline points="0,641 600,744 1200,641" fill="none" stroke="var(--green)" stroke-width="12"/>
  </svg>
  <div class="title-rule" style="left:230px;top:1374px;width:120px;background:#aaa"></div>
  <div class="title-rule" style="left:850px;top:1374px;width:120px;background:#aaa"></div>
  <h2 class="section-title benefits-title" style="top:1350px">Sanivex Aquaclor Benefits</h2>

  <svg class="abs" style="left:0;top:0" width="1200" height="2100" viewBox="0 0 1200 2100">
    <g stroke="#d9d9d9" stroke-width="2">
      <line x1="599" y1="1709" x2="599" y2="1542"/>
      <line x1="599" y1="1709" x2="747" y2="1653"/>
      <line x1="599" y1="1709" x2="702" y2="1831"/>
      <line x1="599" y1="1709" x2="502" y2="1831"/>
      <line x1="599" y1="1709" x2="444" y2="1653"/>
    </g>
  </svg>
  <div class="node" role="img" aria-label="Photo of hospital staff" style="left:537px;top:1480px;width:124px;height:124px"></div>
  <div class="node" role="img" aria-label="Photo of a researcher at an institution" style="left:685px;top:1591px;width:124px;height:124px"></div>
  <div class="node" role="img" aria-label="Photo of pathology lab workers" style="left:640px;top:1769px;width:124px;height:124px"></div>
  <div class="node" role="img" aria-label="Photo of a military family" style="left:440px;top:1769px;width:124px;height:124px"></div>
  <div class="node" role="img" aria-label="Photo of a disaster-struck area" style="left:382px;top:1591px;width:124px;height:124px"></div>
  <div class="seal" style="left:553px;top:1663px;width:92px;height:92px"><span style="width:50px;height:50px"></span></div>

  <div class="benefit-label" style="left:499px;top:1427px;width:200px;text-align:center">Major Hospitals</div>
  <div class="benefit-label" style="left:833px;top:1638px">Institutions</div>
  <div class="benefit-label" style="left:787px;top:1822px">Pathology</div>
  <div class="benefit-label" style="left:218px;top:1822px;width:200px;text-align:right">Military</div>
  <div class="benefit-label" style="left:161px;top:1638px;width:200px;text-align:right">Disaster areas</div>
</section>

<section class="products">
  <div class="title-rule" style="left:240px;top:2083px;width:120px"></div>
  <div class="title-rule" style="left:860px;top:2083px;width:120px"></div>
  <h2 class="section-title" style="top:2059px">Sanivex <em>Aquaclor Products</em></h2>

  <article class="product" style="left:77px">
    <div class="body">
      <div class="pack" role="img" aria-label="Product pack of Aquaclor 500 sachets"></div>
      <p>Aquaclor 500 ® is recommended for areas that have a high risk of exposure and infection. It is recommended for surfaces not directly involved in blood or body fluid spills. Aquaclor 500 ® has been evaluated according to TGA guidelines for hospital grade disinfectant and sanitisers under clean conditions.</p>
    </div>
    <h3>AQUACLOR 500</h3>
  </article>
  <article class="product" style="left:614px">
    <div class="body">
      <div class="pack" role="img" aria-label="Product pack of Aquaclor 5000 sachets"></div>
      <p>Aquaclor 500 ® is recommended for areas that have a high risk of exposure and infection. It is recommended for surfaces not directly involved in blood or body fluid spills. Aquaclor 500 ® has been evaluated according to TGA guidelines for hospital grade disinfectant and sanitisers under clean conditions.</p>
    </div>
    <h3>AQUACLOR 5000</h3>
  </article>
</section>
</main>

<footer class="site-footer">
  <svg class="footer-bg" width="1200" height="590" viewBox="0 0 1200 590" role="img" aria-label="Dimmed photo of surgeons in an operating theatre">
    <defs>
      <linearGradient id="footGrad" x1="0" y1="0" x2="1" y2="1">
        <stop offset="0" stop-color="#3c4449"/>
        <stop offset=".6" stop-color="#2a2f32"/>
        <stop offset="1" stop-color="#232628"/>
      </linearGradient>
    </defs>
    <polygon points="0,40 600,0 1200,40 1200,590 0,590" fill="url(#footGrad)"/>
    <polyline points="0,40 600,0 1200,40" fill="none" stroke="var(--green)" stroke-width="6"/>
  </svg>
  <div class="seal" style="left:550px;top:2514px"><span></span></div>

  <h3 class="footer-heading" style="left:79px">Contact Us</h3>
  <div class="form-head">INQUERY FORM</div>
  <div class="field" style="top:2802px;height:48px">Name :</div>
  <div class="field" style="top:2855px;height:48px">Phone No :</div>
  <div class="field" style="top:2907px;height:48px">Email :</div>
  <div class="field" style="top:2961px;height:75px">Message :</div>
  <a class="btn submit">SUBMIT</a>

  <h3 class="footer-heading" style="left:507px">Recent Blog</h3>
  <div class="post" style="top:2750px">
    <div class="thumb" role="img" aria-label="Blog thumbnail photo"></div>
    <h4>TITLE OF FIRST BLOG</h4>
    <div class="meta">By Admin<svg width="24" height="20" viewBox="0 0 24 20"><ellipse cx="10" cy="8" rx="8" ry="6" fill="var(--green)"/><path d="M4 12l-2 6 6-3z" fill="var(--green)"/></svg>28</div>
  </div>
  <div class="post" style="top:2875px">
    <div class="thumb" role="img" aria-label="Blog thumbnail photo"></div>
    <h4>TITLE OF FIRST BLOG</h4>
    <div class="meta">By Admin<svg width="24" height="20" viewBox="0 0 24 20"><ellipse cx="10" cy="8" rx="8" ry="6" fill="var(--green)"/><path d="M4 12l-2 6 6-3z" fill="var(--green)"/></svg>28</div>
  </div>
  <div class="post" style="top:3000px;border-bottom:none">
    <div class="thumb" role="img" aria-label="Blog thumbnail photo"></div>
    <h4>TITLE OF FIRST BLOG</h4>
    <div class="meta">By Admin<svg width="24" height="20" viewBox="0 0 24 20"><ellipse cx="10" cy="8" rx="8" ry="6" fill="var(--green)"/><path d="M4 12l-2 6 6-3z" fill="var(--green)"/></svg>28</div>
  </div>

  <h3 class="footer-heading" style="left:861px">Get In touch</h3>
  <div class="contact-line" style="top:2750px">
    <svg width="22" height="20" viewBox="0 0 24 22"><path d="M2 4l6-2 8 3 6-2v15l-6 2-8-3-6 2z M8 2v15 M16 5v15" fill="none" stroke="var(--green)" stroke-width="2"/></svg>
    <div><strong>ADDRESS</strong><br><span style="display:block;margin-top:8px">Kanaalweg 14 2611 AB<br>Delfthaven ZH The Netherlands</span></div>
  </div>
  <div class="contact-line" style="top:2870px">
    <svg width="22" height="22" viewBox="0 0 24 24"><path fill="none" stroke="var(--green)" stroke-width="2" d="M6.6 10.8a15.1 15.1 0 0 0 6.6 6.6l2.2-2.2c.3-.3.7-.4 1-.2 1.1.4 2.3.6 3.6.6.6 0 1 .4 1 1V20c0 .6-.4 1-1 1A17 17 0 0 1 3 4c0-.6.4-1 1-1h3.5c.6 0 1 .4 1 1 0 1.3.2 2.5.6 3.6.1.3 0 .7-.2 1z"/></svg>
    <span>1300 555 010</span>
  </div>
  <div class="contact-line" style="top:2948px">
    <svg width="22" height="22" viewBox="0 0 24 24"><path fill="none" stroke="var(--green)" stroke-width="2" d="M6 9V3h12v6M4 9h16v8H4zM7 14h10v7H7z"/></svg>
    <span>1300 555 011</span>
  </div>
  <div class="contact-line" style="top:3016px">
    <svg width="22" height="20" viewBox="0 0 24 20"><rect x="2" y="3" width="20" height="14" fill="none" stroke="var(--green)" stroke-width="2"/><path d="M2 4l10 7 10-7" fill="none" stroke="var(--green)" stroke-width="2"/></svg>
    <span>info@sanivexgroup.example</span>
  </div>

  <div class="bottom-bar">
    <div class="copyright"><svg width="14" height="14" viewBox="0 0 14 14"><circle cx="7" cy="7" r="6" fill="none" stroke="#fff" stroke-width="1.5"/><path d="M9 5a2.5 2.5 0 1 0 0 4" fill="none" stroke="#fff" stroke-width="1.5"/></svg>SANIVEX - 2017 | All Right Reserved</div>
    <nav class="foot-nav"><a href="#">About</a><i>|</i><a href="#">Products</a><i>|</i><a href="#">Downloads</a><i>|</i><a href="#">Media &amp; News</a><i>|</i><a href="#">Contact</a></nav>
  </div>
</footer>

</body>
</html>
```